Health Spectrum and Energy Slides

Create beautiful and facinating PowerPoint slides that inspire and motivate

Target Market(s)

Clients looking for strategic breakthroughs and transformation

Industry/Entity Type

Health

Requirements
Must have
• Beautiful, heartfelt and fascinating graphics.
Nice to have
• Award winning designs.

```html
<!DOCTYPE html>
<html lang="en">
<head>
<meta charset="utf-8">
<title>Your Restaurant</title>
<link href="https://fonts.googleapis.com/css2?family=Roboto+Condensed:wght@700&family=Roboto:wght@400&display=swap" rel="stylesheet">
<style>
  :root {
    --navy: #0a47a5;
    --orange: #ef6a22;
    --teal: #10b9b1;
    --ink: #222222;
    --paper: #ffffff;
  }
  * { margin: 0; padding: 0; box-sizing: border-box; }
  html, body { width: 1200px; height: 720px; overflow: hidden; background: var(--paper); }
  .slide { position: relative; width: 1200px; height: 720px; background: var(--paper); font-family: "Roboto", Arial, sans-serif; }
  .headline { position: absolute; left: 0; width: 1244px; text-align: center; font-family: "Roboto Condensed", "Arial Narrow", sans-serif; font-weight: 700; font-size: 50px; line-height: 1; letter-spacing: 0.5px; }
  .headline--top { top: 66px; color: var(--navy); }
  .headline--main { top: 122px; color: var(--orange); }
  .chef-art { position: absolute; left: 30px; top: 196px; width: 380px; height: 476px; border-radius: 40% 40% 30% 30%; background: radial-gradient(ellipse at 55% 40%, #f3e9df 0%, #ede7e1 45%, #f6f4f2 80%, rgba(255,255,255,0) 100%); }
  .food-label { position: absolute; color: var(--orange); font-size: 33px; line-height: 42px; text-align: center; }
  .food-label--least { left: 466px; top: 214px; width: 160px; }
  .food-label--favorite { left: 902px; top: 226px; width: 160px; }
  .plate-pin { position: absolute; left: 690px; top: 194px; width: 180px; height: 244px; }
  .spectrum { position: absolute; left: 0; top: 514px; width: 1200px; height: 140px; }
  .spectrum-item { position: absolute; width: 120px; margin-left: -60px; text-align: center; }
  .spectrum-dot { display: block; width: 70px; height: 70px; margin: 0 auto; border-radius: 50%; background: var(--teal); box-shadow: inset 0 0 0 6px var(--teal), inset 0 0 0 8px var(--paper); }
  .spectrum-label { display: block; margin-top: 14px; font-size: 17px; line-height: 21px; color: var(--ink); }
</style>
</head>
<body>
<main class="slide">
  <h1 class="headline headline--top">YOUR RESTAURANT:</h1>
  <h2 class="headline headline--main">YOU CAN EAT ANYTHING THAT YOU WANT AT</h2>

  <div class="chef-art" role="img" aria-label="Cartoon chef carrying a tray with a menu framed by carrots, apples and tomatoes"></div>

  <p class="food-label food-label--least">Least<br>Favorite<br>Food</p>

  <svg class="plate-pin" viewBox="0 0 180 244" aria-hidden="true">
    <circle cx="88" cy="80" r="68" fill="none" stroke="var(--teal)" stroke-width="16"/>
    <path d="M74 144 L88 166 L102 144 Z" fill="var(--teal)"/>
    <rect x="82" y="160" width="12" height="80" rx="6" fill="var(--teal)"/>
    <rect x="78" y="196" width="28" height="22" rx="8" fill="var(--teal)"/>
    <circle cx="102" cy="80" r="34" fill="var(--teal)"/>
    <circle cx="102" cy="80" r="27" fill="none" stroke="var(--paper)" stroke-width="2.5"/>
    <ellipse cx="50" cy="68" rx="6" ry="10" fill="var(--teal)"/>
    <rect x="47.5" y="70" width="5" height="38" rx="2.5" fill="var(--teal)"/>
    <path d="M58 58 v14 q0 6 6 6 q6 0 6 -6 v-14 M64 58 v14" fill="none" stroke="var(--teal)" stroke-width="2.5"/>
    <rect x="61.5" y="74" width="5" height="34" rx="2.5" fill="var(--teal)"/>
  </svg>

  <p class="food-label food-label--favorite">Favorite<br>Food</p>

  <ul class="spectrum" style="list-style:none">
    <li class="spectrum-item" style="left:410px"><span class="spectrum-dot"></span><span class="spectrum-label">Neutral<br>Food</span></li>
    <li class="spectrum-item" style="left:523px"><span class="spectrum-dot"></span><span class="spectrum-label">Heartfelt<br>Desire</span></li>
    <li class="spectrum-item" style="left:649px"><span class="spectrum-dot"></span><span class="spectrum-label">Uncomfortable<br>Emotions</span></li>
    <li class="spectrum-item" style="left:776px"><span class="spectrum-dot"></span><span class="spectrum-label">Pleasurable<br>Emotions</span></li>
    <li class="spectrum-item" style="left:892px"><span class="spectrum-dot"></span><span class="spectrum-label">Painful<br>Emotions</span></li>
    <li class="spectrum-item" style="left:1002px"><span class="spectrum-dot"></span><span class="spectrum-label">Neutral<br>Emotions</span></li>
    <li class="spectrum-item" style="left:1106px"><span class="spectrum-dot"></span><span class="spectrum-label">Favorite<br>Emotions</span></li>
  </ul>
</main>
</body>
</html>
```